Environmental Plastics Infographic

We need a series of infographics that can be used individually or as a combined presentation. We'd like the combined piece to include an introduction and conclusion along with 4-5 infographics. Each infographic (information unit) should also work as a standalone. We are trying to help people visualize size proportions and ratios to put carbon footprint/life cycle data for EPS foam packaging in perspective. We are looking for something creative to help people understand what the figures represent in terms they are familiar with.
To view our typical company design/style please see our website at www.lunarfoldhub.org. Our primary RGB colors are: (187,140,9); (94,47,29); (94,138,164); and (164,167,15). Secondary RGB colors are (249,162,28) and (218,210,208). Our title/header font is DIN Next LT Pro and our copy font is Calibri 10.5 pt. We can deviate from the font specification if beneficial and welcome interesting text treatments and typography.
We want sufficient white space with easy to grasp message concept with visual components. The attachment showing data points present concepts on how to show the data impacts but are only representative of a baseline concept - we are confident a professional designer can do a much better job with better visual presentation.
Target Market(s)
The audience is international brand manufacturers (kestrova, vexa), US legislators & government agencies.
Nice to have
- Other creative ideas on how to present this messaging is encouraged.

```html
<!DOCTYPE html>
<html lang="en">
<head>
<meta charset="utf-8">
<title>EPS Life Cycle Infographics</title>
<link href="https://fonts.googleapis.com/css2?family=Barlow+Condensed:wght@500;600;700&family=Barlow:wght@500;600;700;800&display=swap" rel="stylesheet">
<style>
:root{
  --olive:#a4a70f;
  --brown:#5e2f1d;
  --blue:#5e8aa4;
  --gold:#bb8c09;
  --orange:#f9a21c;
  --stone:#dad2d0;
  --white:#ffffff;
}
*{margin:0;padding:0;box-sizing:border-box}
html,body{width:1109px;height:1200px;overflow:hidden;background:var(--white)}
body{position:relative;font-family:"Barlow Condensed",sans-serif;color:var(--brown)}
.panel{position:absolute;width:548px;height:404px;overflow:hidden}
.header{position:absolute;left:0;top:0;width:548px;height:107px;background:var(--olive)}
.header .series{position:absolute;right:434px;top:24px;text-align:right;font-weight:700;font-size:27px;line-height:23px;color:var(--brown)}
.header .title{position:absolute;left:125px;top:20px;font-weight:700;font-size:44px;line-height:37px;color:var(--white);white-space:nowrap}
.header .emblem{position:absolute;left:410px;top:8px}
.t{position:absolute;white-space:nowrap;font-weight:600}
.hl{color:var(--orange)}
.olive{color:var(--olive)}
.org{position:absolute;left:33px;top:327px;display:flex;align-items:center;gap:5px}
.org .dot{width:28px;height:28px;border-radius:50%;background:var(--gold)}
.org .name{font-family:"Barlow",sans-serif;font-weight:500;font-size:8px;color:var(--brown)}
.url{position:absolute;left:33px;top:363px;font-family:"Barlow",sans-serif;font-weight:700;font-size:8.5px;color:var(--brown)}
.summary{position:absolute;right:26px;top:334px;text-align:right}
.summary .label{font-weight:700;font-size:21px;line-height:22px;color:var(--olive)}
.summary .fact{font-weight:600;font-size:19px;line-height:22px;color:var(--brown)}
.summary .source{font-family:"Barlow",sans-serif;font-size:5.5px;color:var(--orange);font-style:italic}
svg.art{position:absolute;left:0;top:0}
.lede{font-family:"Barlow",sans-serif;font-weight:500;font-size:11.4px;color:var(--brown)}
</style>
</head>
<body>

<!-- Global warming: car vs EPS -->
<section class="panel" style="left:0;top:0">
  <div class="header">
    <div class="series">EPS<br>LIFE<br>CYCLE</div>
    <div class="title">GLOBAL<br>WARMING</div>
    <svg class="emblem" width="120" height="100"><circle cx="55" cy="52" r="46" fill="rgba(255,255,255,.22)" role="img" aria-label="Recycling swirl emblem"/></svg>
  </div>
  <svg class="art" width="548" height="404">
    <rect x="165" y="237" width="216" height="21" fill="var(--blue)"/>
    <line x1="172" y1="247.5" x2="378" y2="247.5" stroke="var(--white)" stroke-width="3" stroke-dasharray="9 6"/>
    <circle cx="98" cy="232" r="70" fill="url(#carFill)" stroke="var(--blue)" stroke-width="5" role="img" aria-label="Photo of an orange hatchback car"/>
    <circle cx="451" cy="232" r="70" fill="url(#epsFill)" stroke="var(--blue)" stroke-width="5" role="img" aria-label="Photo of white EPS foam packaging pieces"/>
    <defs>
      <radialGradient id="carFill"><stop offset="0" stop-color="#e58a2a"/><stop offset=".6" stop-color="#f3e6d8"/><stop offset="1" stop-color="#fff"/></radialGradient>
      <radialGradient id="epsFill"><stop offset="0" stop-color="#d9d9d9"/><stop offset="1" stop-color="#fff"/></radialGradient>
    </defs>
    <path d="M155 167 q15 -10 30 -9" fill="none" stroke="var(--olive)" stroke-width="2" stroke-dasharray="5 4"/>
    <path d="M180 153 l6 5 -7 3" fill="none" stroke="var(--olive)" stroke-width="2"/>
    <path d="M380 277 q-10 15 -30 15" fill="none" stroke="var(--olive)" stroke-width="2" stroke-dasharray="5 4"/>
    <path d="M356 286 l-7 6 7 4" fill="none" stroke="var(--olive)" stroke-width="2"/>
    <g fill="var(--olive)">
      <path d="M185 193 a18 18 0 0 1 36 0 z"/><path d="M253 193 a18 18 0 0 1 36 0 z"/><path d="M323 193 a18 18 0 0 1 36 0 z"/>
    </g>
    <g stroke="var(--white)" stroke-width="2">
      <line x1="203" y1="191" x2="195" y2="183"/><line x1="271" y1="191" x2="276" y2="180"/><line x1="341" y1="191" x2="349" y2="178"/>
    </g>
    <g fill="var(--olive)">
      <rect x="224" y="287" width="14" height="9"/><rect x="236" y="294" width="22" height="8"/><rect x="223" y="300" width="38" height="9" rx="4"/>
    </g>
    <g fill="var(--white)"><circle cx="229" cy="305" r="2"/><circle cx="236" cy="305" r="2"/><circle cx="243" cy="305" r="2"/><circle cx="250" cy="305" r="2"/><circle cx="257" cy="305" r="2"/></g>
  </svg>
  <div class="t lede" style="left:29px;top:122px">EPS HAS A <span class="hl">VERY LOW</span> GLOBAL WARMING IMPACT COMPARED TO OTHER PACKAGING MATERIALS</div>
  <div class="t" style="left:206px;top:151px;font-size:15px">CAR CARBON FOOTPRINT</div>
  <div class="t" style="left:173px;top:198px;width:60px;text-align:center;font-size:11px">1 km<br><span class="hl" style="font-size:11px">115.5 kg CO2</span></div>
  <div class="t" style="left:241px;top:198px;width:60px;text-align:center;font-size:11px">50 km<br><span class="hl" style="font-size:11px">5,775 kg CO2</span></div>
  <div class="t" style="left:309px;top:198px;width:66px;text-align:center;font-size:11px">100 km<br><span class="hl" style="font-size:11px">11,550 kg CO2</span></div>
  <div class="t" style="left:206px;top:264px;font-size:15px">EPS CARBON FOOTPRINT</div>
  <div class="t" style="left:270px;top:284px;font-size:11px;line-height:15px">1 ton of EPS<br><span class="hl" style="font-size:11px">5,360 kg CO2</span></div>
  <div class="org"><span class="dot"></span><span class="name">Lunarfold Hub</span></div>
  <div class="url">www.lunarfoldhub.org</div>
  <div class="summary"><div class="label">CARBON FOOTPRINT</div><div class="fact">1 Ton EPS = Driving Car 31 Miles</div><div class="source">https://co2.carbonreckon.org/en/car_calculators</div></div>
</section>

<!-- Non-renewable energy use -->
<section class="panel" style="left:561px;top:0">
  <div class="header">
    <div class="series">EPS<br>LIFE<br>CYCLE</div>
    <div class="title">NON-RENEWABLE<br>ENERGY USE</div>
    <svg class="emblem" width="140" height="100" style="left:400px"><circle cx="65" cy="52" r="46" fill="rgba(255,255,255,.22)" role="img" aria-label="Recycling swirl emblem"/></svg>
  </div>
  <svg class="art" width="548" height="404">
    <circle cx="98" cy="232" r="70" fill="url(#bulbFill)" stroke="var(--blue)" stroke-width="5" role="img" aria-label="Photo of a glowing incandescent lightbulb"/>
    <circle cx="449" cy="232" r="70" fill="url(#epsFill2)" stroke="var(--blue)" stroke-width="5" role="img" aria-label="Photo of white EPS foam packaging pieces"/>
    <defs>
      <radialGradient id="bulbFill"><stop offset="0" stop-color="#f1c56a"/><stop offset=".55" stop-color="#e9dcc0"/><stop offset="1" stop-color="#fff"/></radialGradient>
      <radialGradient id="epsFill2"><stop offset="0" stop-color="#d9d9d9"/><stop offset="1" stop-color="#fff"/></radialGradient>
    </defs>
    <path d="M290 161 L266 240 L281 238 L264 303 L298 225 L283 227 Z" fill="var(--blue)"/>
    <g fill="var(--olive)" stroke="var(--olive)">
      <circle cx="222" cy="193" r="12" stroke="none"/><rect x="216" y="203" width="12" height="12" stroke="none"/>
      <g stroke-width="2.5"><line x1="222" y1="172" x2="222" y2="176"/><line x1="202" y1="193" x2="206" y2="193"/><line x1="238" y1="193" x2="242" y2="193"/><line x1="208" y1="179" x2="211" y2="182"/><line x1="236" y1="179" x2="233" y2="182"/><line x1="208" y1="207" x2="211" y2="204"/><line x1="236" y1="207" x2="233" y2="204"/></g>
    </g>
    <g fill="var(--olive)"><rect x="302" y="242" width="18" height="12"/><rect x="318" y="252" width="28" height="10"/><rect x="300" y="260" width="53" height="16" rx="7"/></g>
    <g fill="var(--white)"><circle cx="309" cy="268" r="3"/><circle cx="319" cy="268" r="3"/><circle cx="329" cy="268" r="3"/><circle cx="339" cy="268" r="3"/></g>
    <path d="M384 165 q-20 -10 -35 5" fill="none" stroke="var(--olive)" stroke-width="2" stroke-dasharray="5 4"/>
    <path d="M346 164 l2 8 7 -3" fill="none" stroke="var(--olive)" stroke-width="2"/>
    <path d="M153 304 q20 18 50 0" fill="none" stroke="var(--olive)" stroke-width="2" stroke-dasharray="5 4"/>
    <path d="M200 296 l3 8 -8 1" fill="none" stroke="var(--olive)" stroke-width="2"/>
  </svg>
  <div class="t" style="left:181px;top:240px;font-size:14px;line-height:17px">ONE 100 WATT<br>LIGHTBULB<br><span class="hl">= 360 MJ</span></div>
  <div class="t" style="left:288px;top:188px;font-size:14px;line-height:17px">1 TON OF EPS<br><span class="hl">= 108,000 MJ</span></div>
  <div class="org"><span class="dot"></span><span class="name">Lunarfold Hub</span></div>
  <div class="url">www.lunarfoldhub.org</div>
  <div class="summary"><div class="label">ENERGY CONSUMPTION</div><div class="fact">1 Ton EPS = 300 Hours Lightbulb</div><div class="source">https://www.wattcensus.gov/articles/how-much-do-you-consume</div></div>
</section>

<!-- Global warming: landfill diversion -->
<section class="panel" style="left:0;top:404px">
  <div class="header">
    <div class="series">EPS<br>LIFE<br>CYCLE</div>
    <div class="title">GLOBAL<br>WARMING</div>
    <svg class="emblem" width="120" height="100"><circle cx="55" cy="52" r="46" fill="rgba(255,255,255,.22)" role="img" aria-label="Recycling swirl emblem"/></svg>
  </div>
  <svg class="art" width="548" height="404">
    <path d="M180 146 q80 -45 159 -2" fill="none" stroke="var(--olive)" stroke-width="2" stroke-dasharray="6 4"/>
    <path d="M332 138 l7 6 -8 4" fill="none" stroke="var(--olive)" stroke-width="2"/>
    <g fill="var(--olive)">
      <circle cx="80" cy="272" r="36"/><circle cx="301" cy="190" r="36"/><circle cx="387" cy="190" r="36"/><circle cx="473" cy="190" r="36"/><circle cx="301" cy="272" r="36"/><circle cx="473" cy="272" r="36"/>
    </g>
    <g fill="none" stroke="var(--white)" stroke-width="2.2">
      <rect x="283" y="178" width="36" height="26"/><path d="M289 199 l8 -10 6 6 4 -4 8 8 z" fill="var(--white)"/><path d="M290 178 l11 -10 11 10"/>
      <ellipse cx="387" cy="190" rx="9" ry="24"/><line x1="392" y1="170" x2="382" y2="210"/>
      <path d="M473 171 a4 4 0 1 1 2 6 l0 4 l-21 13 h42 l-21 -13"/>
      <rect x="283" y="260" width="36" height="24" rx="2"/><rect x="290" y="266" width="22" height="12"/>
      <path d="M473 255 l14 24 h-28 z"/>
    </g>
    <g fill="var(--white)">
      <circle cx="68" cy="252" r="4"/><rect x="63" y="258" width="10" height="20"/><rect x="63" y="278" width="4" height="14"/><rect x="69" y="278" width="4" height="14"/>
      <path d="M84 266 h16 l-2 24 h-12 z"/><rect x="83" y="262" width="18" height="3"/>
    </g>
    <text x="473" y="276" text-anchor="middle" font-family="Barlow, sans-serif" font-weight="700" font-size="13" fill="var(--white)">6</text>
    <text x="473" y="294" text-anchor="middle" font-family="Barlow, sans-serif" font-weight="700" font-size="10" fill="var(--white)">PS</text>
  </svg>
  <div class="t" style="left:42px;top:142px;font-family:Barlow,sans-serif;font-weight:800;font-size:46px;line-height:46px;color:var(--orange)">19,850 <span style="color:var(--brown);font-size:24px;font-weight:800">TONS</span></div>
  <div class="t" style="left:44px;top:189px;font-family:Barlow,sans-serif;font-weight:700;font-size:12.3px">EPS diverted from the landfill in 2018</div>
  <div class="t" style="left:44px;top:205px;font-weight:700;font-size:30px;line-height:30px">THE EQUIVALENT OF</div>
  <div class="t" style="left:126px;top:235px;font-size:15px">WASTE GENERATED BY</div>
  <div class="t" style="left:124px;top:249px;font-family:Barlow,sans-serif;font-weight:800;font-size:45px;line-height:44px;color:var(--orange)">13,233</div>
  <div class="t" style="left:126px;top:292px;font-size:20px">U.S. HOUSEHOLDS</div>
  <div class="t" style="left:343px;top:240px;font-size:17px;line-height:19px"><span style="font-size:23px;font-weight:700">RECYCLED</span><br>CONTENT EPS<br>PACKAGING</div>
  <div class="org"><span class="dot"></span><span class="name">Lunarfold Hub</span></div>
  <div class="url">www.lunarfoldhub.org</div>
</section>

<!-- Water consumption: swimming pool -->
<section class="panel" style="left:561px;top:404px">
  <div class="header">
    <div class="series">EPS<br>LIFE<br>CYCLE</div>
    <div class="title">WATER<br>CONSUMPTION</div>
    <svg class="emblem" width="140" height="100" style="left:400px"><circle cx="65" cy="52" r="46" fill="rgba(255,255,255,.22)" role="img" aria-label="Recycling swirl emblem"/></svg>
  </div>
  <svg class="art" width="548" height="404">
    <g fill="none" stroke="var(--blue)" stroke-width="4">
      <path d="M162 210 q7.5 -7 15 0 t15 0 t15 0 t15 0 t15 0 t15 0 t15 0 t15 0 t15 0 t15 0 t15 0 t15 0 t15 0 t15 0 t15 0"/>
      <path d="M162 225 q7.5 -7 15 0 t15 0 t15 0 t15 0 t15 0 t15 0 t15 0 t15 0 t15 0 t15 0 t15 0 t15 0 t15 0 t15 0 t15 0"/>
      <path d="M162 240 q7.5 -7 15 0 t15 0 t15 0 t15 0 t15 0 t15 0 t15 0 t15 0 t15 0 t15 0 t15 0 t15 0 t15 0 t15 0 t15 0"/>
    </g>
    <circle cx="98" cy="232" r="70" fill="url(#poolFill)" stroke="var(--blue)" stroke-width="5" role="img" aria-label="Photo of a rectangular blue swimming pool"/>
    <circle cx="451" cy="232" r="70" fill="url(#boxFill)" stroke="var(--blue)" stroke-width="5" role="img" aria-label="Photo of a white EPS shipping container"/>
    <defs>
      <radialGradient id="poolFill"><stop offset="0" stop-color="#35aee0"/><stop offset=".5" stop-color="#bfe3f2"/><stop offset="1" stop-color="#fff"/></radialGradient>
      <radialGradient id="boxFill"><stop offset="0" stop-color="#e2e2e2"/><stop offset="1" stop-color="#fff"/></radialGradient>
      <path id="ring" d="M391 222 a60 60 0 0 0 118 24"/>
    </defs>
    <text font-family="Barlow, sans-serif" font-size="8" fill="var(--blue)"><textPath href="#ring">A typical EPS shipping container 15x13x12 inches</textPath></text>
    <path d="M201 254 q-14 18 -14 26 a14 14 0 0 0 28 0 q0 -8 -14 -26z" fill="var(--olive)"/>
    <path d="M136 147 q15 -5 30 0" fill="none" stroke="var(--olive)" stroke-width="2" stroke-dasharray="5 4"/>
    <path d="M160 143 l6 4 -6 4" fill="none" stroke="var(--olive)" stroke-width="2"/>
    <path d="M393 302 q-15 10 -30 0" fill="none" stroke="var(--olive)" stroke-width="2" stroke-dasharray="5 4"/>
    <path d="M369 297 l-6 5 7 3" fill="none" stroke="var(--olive)" stroke-width="2"/>
  </svg>
  <div class="t" style="left:177px;top:158px;font-size:15px;line-height:19px">ONE 40X20 FOOT SWIMMING POOL<br>(AVG 4 FT DEPTH) <span class="hl">24,000 GALLONS</span></div>
  <div class="t" style="left:231px;top:249px;font-size:15px;line-height:19px">1 TON OF EPS FOAM USE<br><span class="hl">XXX GALLONS</span> WATER TO<br>MANUFACTURE</div>
  <div class="org"><span class="dot"></span><span class="name">Lunarfold Hub</span></div>
  <div class="url">www.lunarfoldhub.org</div>
  <div class="summary"><div class="label">WATER CONSUMPTION</div><div class="fact">1,000 EPS Shipping Containers = xx Swimming Pools</div></div>
</section>

<!-- Global warming: national totals -->
<section class="panel" style="left:0;top:808px">
  <div class="header">
    <div class="series">EPS<br>LIFE<br>CYCLE</div>
    <div class="title">GLOBAL<br>WARMING</div>
    <svg class="emblem" width="120" height="100"><circle cx="55" cy="52" r="46" fill="rgba(255,255,255,.22)" role="img" aria-label="Recycling swirl emblem"/></svg>
  </div>
  <svg class="art" width="548" height="404">
    <circle cx="98" cy="232" r="72" fill="var(--brown)"/>
    <path d="M98 232 L92 160.3 A72 72 0 0 1 98 160 Z" fill="var(--olive)"/>
    <path d="M95 160 q5 -30 50 -35 q35 -2 55 10" fill="none" stroke="var(--olive)" stroke-width="2" stroke-dasharray="6 4"/>
    <path d="M194 129 l7 6 -8 4" fill="none" stroke="var(--olive)" stroke-width="2"/>
    <path d="M112 310 q30 40 85 10" fill="none" stroke="var(--brown)" stroke-width="2" stroke-dasharray="6 4"/>
    <path d="M190 315 l8 4 -4 8" fill="none" stroke="var(--brown)" stroke-width="2"/>
    <path d="M188 151 H521 V210 a18 18 0 0 1 -18 18 H188 Z" fill="none" stroke="var(--olive)" stroke-width="2.5"/>
    <path d="M188 313 H521 V254 a18 18 0 0 0 -18 -18 H188 Z" fill="none" stroke="var(--brown)" stroke-width="2.5"/>
    <circle cx="222" cy="190" r="26" fill="var(--olive)"/>
    <rect x="207" y="184" width="30" height="13" fill="var(--white)" role="img" aria-label="EPS foam pieces"/>
    <circle cx="222" cy="274" r="26" fill="var(--brown)"/>
    <path d="M204 279 q0 -7 7 -8 l5 -5 h12 l6 5 q6 1 6 8 z" fill="var(--white)"/>
    <circle cx="211" cy="280" r="3" fill="var(--brown)"/><circle cx="233" cy="280" r="3" fill="var(--brown)"/>
  </svg>
  <div class="t" style="left:261px;top:160px;font-size:12.6px;line-height:21.5px">EPS U.S. MANUFACTURING IN 2017 WAS <span class="hl">6.35 MILLION TONS</span><br>EACH TON OF EPS PRODUCTION EMITS <span class="hl">.5360 KG/TN CO2</span><br>TOTAL CO2 IMPACT = <span class="hl">3.5 MILLION TONS</span></div>
  <div class="t" style="left:261px;top:245px;font-size:12.6px;line-height:21.5px"><span class="hl">272.48 MILLION CARS</span> REGISTERED IN THE U.S. IN 2017<br>EACH CAR EMITS AN AVERAGE OF <span class="hl">7 TNS OF CO2/YEAR</span><br>TOTAL CO2 IMPACT = <span class="hl">1.907 BILLION TONS</span></div>
  <div class="org"><span class="dot"></span><span class="name">Lunarfold Hub</span></div>
  <div class="url">www.lunarfoldhub.org</div>
</section>

<!-- Water consumption: EPS vs corrugated -->
<section class="panel" style="left:561px;top:808px">
  <div class="header">
    <div class="series">EPS<br>LIFE<br>CYCLE</div>
    <div class="title">WATER<br>CONSUMPTION</div>
    <svg class="emblem" width="140" height="100" style="left:400px"><circle cx="65" cy="52" r="46" fill="rgba(255,255,255,.22)" role="img" aria-label="Recycling swirl emblem"/></svg>
  </div>
  <svg class="art" width="548" height="404">
    <g fill="none" stroke="var(--blue)" stroke-width="4">
      <path d="M162 232 q7.5 -7 15 0 t15 0 t15 0 t15 0 t15 0 t15 0 t15 0 t15 0 t15 0 t15 0 t15 0 t15 0 t15 0 t15 0 t15 0"/>
      <path d="M162 247 q7.5 -7 15 0 t15 0 t15 0 t15 0 t15 0 t15 0 t15 0 t15 0 t15 0 t15 0 t15 0 t15 0 t15 0 t15 0 t15 0"/>
    </g>
    <circle cx="98" cy="232" r="70" fill="url(#epsFill3)" stroke="var(--blue)" stroke-width="5" role="img" aria-label="Photo of white EPS foam blocks and trays"/>
    <circle cx="450" cy="232" r="70" fill="url(#cardFill)" stroke="var(--blue)" stroke-width="5" role="img" aria-label="Photo of corrugated cardboard boxes"/>
    <defs>
      <radialGradient id="epsFill3"><stop offset="0" stop-color="#dcdcdc"/><stop offset="1" stop-color="#fff"/></radialGradient>
      <radialGradient id="cardFill"><stop offset="0" stop-color="#b88a5a"/><stop offset=".6" stop-color="#e8d6c2"/><stop offset="1" stop-color="#fff"/></radialGradient>
    </defs>
    <path d="M318 162 q-16 22 -16 32 a16 16 0 0 0 32 0 q0 -10 -16 -32z" fill="var(--olive)"/>
    <path d="M230 252 q-16 22 -16 32 a16 16 0 0 0 32 0 q0 -10 -16 -32z" fill="var(--olive)"/>
    <path d="M148 143 q18 -12 40 0" fill="none" stroke="var(--olive)" stroke-width="2" stroke-dasharray="5 4"/>
    <path d="M182 137 l6 6 -7 3" fill="none" stroke="var(--olive)" stroke-width="2"/>
    <path d="M387 297 q-15 8 -32 0" fill="none" stroke="var(--olive)" stroke-width="2" stroke-dasharray="5 4"/>
    <path d="M361 292 l-6 5 7 3" fill="none" stroke="var(--olive)" stroke-width="2"/>
  </svg>
  <div class="t" style="left:212px;top:160px;font-size:16px;line-height:19px">1 TON USE<br><span class="olive">XXX GALLONS</span><br>OF WATER</div>
  <div class="t" style="left:261px;top:257px;font-size:16px;line-height:19px">1 TON USE<br><span class="olive">XXX GALLONS</span><br>OF WATER</div>
  <div class="org"><span class="dot"></span><span class="name">Lunarfold Hub</span></div>
  <div class="url">www.lunarfoldhub.org</div>
  <div class="summary"><div class="label">WATER CONSUMPTION</div><div class="fact">1,000 EPS Shipping Containers &lt; Corrugated Paper</div></div>
</section>

</body>
</html>
```